Business Card Design for Marketing Firm

Looking for business card design for higher end marketing firm. Clean but impressionable/trendy. We are a marketing firm that represents manufacturers in the foodservice equipment and supply industry. Our customers are end users such has hotels, restaurants, country clubs, convention centers and casinos as well as distributors of restaurants supplies and equipment, and manufacturers of foodservice equipment and supplies.
Target Market(s)
Hotels, Restaurants, Supply & Equipment Distributors, Foodservice Manufacturers
Industry/Entity Type
Foodservice/Hospitality
Contact Information for Business Card
Name, Title, Contact Number, Email, Website, Social Media, Address
Requirements
Must have
- Clean & Simple but Serious and Impressionable

```html
<!DOCTYPE html>
<html lang="en">
<head>
<meta charset="utf-8">
<title>Meridian Service Reps — Business Card</title>
<link rel="stylesheet" href="https://fonts.googleapis.com/css2?family=Arimo:wght@400;700&display=swap">
<style>
  :root {
    --backdrop: #2e2e2e;
    --card: #000000;
    --brand-blue: #0a0f9c;
    --ink-light: #ffffff;
    --card-w: 600px;
    --card-h: 343px;
  }
  * { box-sizing: border-box; margin: 0; padding: 0; }
  html, body {
    width: 1200px; height: 1015px; overflow: hidden;
    background: var(--backdrop);
  }
  .canvas {
    width: 1200px; height: 1015px;
    display: flex; flex-direction: column; align-items: center; justify-content: center;
    gap: 60px;
  }
  .card {
    position: relative;
    width: var(--card-w); height: var(--card-h);
    background: var(--card);
    box-shadow: 0 14px 30px rgba(0,0,0,.55);
    overflow: hidden;
    font-family: "Arimo", sans-serif;
  }
  .card__band {
    position: absolute; left: 0; right: 0; bottom: 14px;
    height: 9px; background: var(--brand-blue);
  }

  /* Front */
  .front__brand {
    position: absolute; left: 0; right: 0; top: 112px;
    text-align: center;
  }
  .front__name {
    font-size: 30px; font-weight: 700; letter-spacing: 2px; line-height: 1;
    color: var(--brand-blue); text-transform: uppercase;
  }
  .front__rule {
    width: 380px; height: 1.5px; background: var(--brand-blue);
    margin: 18px auto 0;
  }
  .front__social {
    position: absolute; left: 0; right: 0; top: 200px;
    display: flex; justify-content: center; gap: 12px;
  }
  .social-dot {
    width: 30px; height: 30px; border-radius: 50%;
    border: 2px solid var(--ink-light);
  }

  /* Back */
  .back__details {
    position: absolute; left: 60px; top: 60px;
    color: var(--ink-light);
  }
  .back__person {
    font-size: 21px; font-weight: 700; color: var(--brand-blue);
    letter-spacing: .5px; text-transform: uppercase; line-height: 1.1;
  }
  .back__title {
    font-size: 13px; text-transform: uppercase; letter-spacing: .3px; margin-top: 2px;
  }
  .back__rule {
    width: 120px; height: 1px; background: var(--brand-blue); margin: 14px 0;
  }
  .contact-list { list-style: none; }
  .contact-list li {
    display: flex; align-items: center; gap: 10px;
    font-size: 16px; line-height: 1.45;
  }
  .contact-list svg { width: 15px; height: 15px; flex: none; }
  .back__address { font-size: 16px; line-height: 1.3; padding-left: 25px; }
  .back__wordmark {
    position: absolute; right: 40px; top: 76px;
    font-weight: 700; font-size: 48px; line-height: 1;
    color: var(--brand-blue); text-transform: uppercase; letter-spacing: 1px;
  }
</style>
</head>
<body>
<main class="canvas">

  <section class="card card--front" aria-label="Card front">
    <div class="front__brand">
      <p class="front__name">Meridian Service Reps</p>
      <div class="front__rule"></div>
    </div>
    <div class="front__social" aria-label="Social media links">
      <span class="social-dot"></span>
      <span class="social-dot"></span>
      <span class="social-dot"></span>
    </div>
    <div class="card__band"></div>
  </section>

  <section class="card card--back" aria-label="Card back">
    <div class="back__details">
      <p class="back__person">Daniel Rivers</p>
      <p class="back__title">Managing Director</p>
      <div class="back__rule"></div>
      <ul class="contact-list">
        <li>
          <svg viewBox="0 0 24 24" fill="var(--brand-blue)"><path d="M6.6 10.8a15.1 15.1 0 0 0 6.6 6.6l2.2-2.2a1 1 0 0 1 1-.25 11.4 11.4 0 0 0 3.6.57 1 1 0 0 1 1 1V20a1 1 0 0 1-1 1A17 17 0 0 1 3 4a1 1 0 0 1 1-1h3.5a1 1 0 0 1 1 1c0 1.25.2 2.45.57 3.57a1 1 0 0 1-.25 1z"/></svg>
          044-555 018 274
        </li>
        <li>
          <svg viewBox="0 0 24 24" fill="var(--brand-blue)"><path d="M2 5h20v14H2z M3 6l9 7 9-7" stroke="#000" stroke-width="1.5"/></svg>
          hello@meridianreps.com
        </li>
        <li>
          <svg viewBox="0 0 24 24" fill="none" stroke="var(--brand-blue)" stroke-width="2"><circle cx="12" cy="12" r="9"/><path d="M3 12h18M12 3c3 3 3 15 0 18M12 3c-3 3-3 15 0 18"/></svg>
          www.meridianreps.com
        </li>
      </ul>
      <div class="back__rule"></div>
      <p class="back__address">88 Harbor Lane, Suite 4<br>45120, Portland</p>
    </div>
    <p class="back__wordmark">Meridian</p>
    <div class="card__band"></div>
  </section>

</main>
</body>
</html>
```